Food and Beverage Business Cards

We need business cards with logo designs for a consultant in the food and beverage industry. We specialize in helping restaurants fix operational and management problems.
Specific areas of expertise include:
-Steps of service
-Staff management tools
-Standard operating procedures
-Profit and loss management
-Inventory
-Point of sales
-Bar Menu
-Mystery shopper service
-Handling and managing suppliers

Target Market(s)

Restaurant and bar owners and managers

Industry/Entity Type

Business

Contact Information for Business Card

Mathieu Girardot
Q&T Consulting
phone: 15027390614
mathqt@sampleinbox.com

Font styles to use
Other font styles liked:
• Check out the screen shot font idea

Colors

Designer to choose colors to be used in the design.

Requirements
Must have
• Must include QR code (See attachment)
• Logo should reflect our specific focus on the drinks side of the industry.
• Areas of Expertise:
• -Service Steps
• -Staff management tools
• -S.O.P
• -P&L Management
• -Inventory
• -P.O.S
• -Bar Menu
• -Mystery Shopper Service
• -Handling and Managing Suppliers

```html
<!DOCTYPE html>
<html lang="en">
<head>
<meta charset="utf-8">
<title>Q&amp;T Consulting – Business Cards</title>
<link rel="stylesheet" href="https://fonts.googleapis.com/css2?family=Roboto:wght@400;500;700&display=swap">
<style>
  :root {
    --bg: #3a3a3a;
    --card: #1c1c1c;
    --ink: #ffffff;
    --ink-soft: #e9e9e9;
    --badge: #cfcfcf;
    --badge-accent: #bfe6c2;
  }
  * { box-sizing: border-box; margin: 0; padding: 0; }
  html, body {
    width: 1200px; height: 900px; overflow: hidden;
    background: var(--bg);
    font-family: "Roboto", Arial, sans-serif;
    color: var(--ink);
  }
  .stage { position: relative; width: 1200px; height: 900px; }
  .card {
    position: absolute; left: 270px; width: 660px; height: 377px;
    background: var(--card);
    box-shadow: 0 10px 30px rgba(0,0,0,.45);
  }
  .card--front { top: 56px; }
  .card--back { top: 466px; }

  .brand {
    position: absolute; top: 56px; left: 0; right: 0;
    text-align: center;
    font-weight: 700; font-size: 68px; letter-spacing: 2px; line-height: 1;
    color: var(--ink);
  }
  .badges {
    position: absolute; top: 26px; right: 26px;
    display: flex; gap: 8px;
  }
  .badge { width: 42px; height: 42px; border-radius: 50%; background: var(--badge); }
  .badge--light { background: var(--badge-accent); }

  .expertise {
    position: absolute; top: 176px; left: 40px; right: 40px;
    text-align: center;
  }
  .expertise__title { font-weight: 700; font-size: 19px; margin-bottom: 10px; }
  .expertise__list {
    list-style: none;
    font-size: 16px; line-height: 1.3; color: var(--ink-soft);
  }

  .person {
    position: absolute; top: 152px; right: 396px; text-align: right;
  }
  .person__name { font-weight: 700; font-size: 24px; letter-spacing: .5px; text-transform: uppercase; }
  .person__role { font-weight: 500; font-size: 17px; letter-spacing: .5px; text-transform: uppercase; margin-top: 4px; }
  .divider {
    position: absolute; left: 286px; top: 142px;
    width: 2px; height: 92px; background: var(--ink);
  }
  .contact {
    position: absolute; left: 312px; top: 170px;
    list-style: none; font-size: 17px; line-height: 1.5;
  }
  .contact__item { display: flex; align-items: center; gap: 10px; }
  .contact__icon { width: 15px; height: 15px; fill: var(--ink); }
</style>
</head>
<body>
<main class="stage">
  <section class="card card--front">
    <div class="badges">
      <span class="badge"></span>
      <span class="badge"></span>
      <span class="badge badge--light"></span>
    </div>
    <h1 class="brand">Q&amp;T Harbor</h1>
    <div class="expertise">
      <h2 class="expertise__title">Areas of Expertise</h2>
      <ul class="expertise__list">
        <li>Service Steps | Staff management tools | S.O.P | P&amp;L Management</li>
        <li>Inventory | P.O.S | Bar Menu | Mystery Shopper Service</li>
        <li>Handling and Managing Suppliers</li>
      </ul>
    </div>
  </section>

  <section class="card card--back">
    <div class="person">
      <p class="person__name">Mathieu Girardot</p>
      <p class="person__role">Q&amp;T Consulting</p>
    </div>
    <span class="divider"></span>
    <ul class="contact">
      <li class="contact__item">
        <svg class="contact__icon" viewBox="0 0 24 24" aria-hidden="true"><path d="M6.6 10.8a15.1 15.1 0 0 0 6.6 6.6l2.2-2.2a1 1 0 0 1 1-.25 11.4 11.4 0 0 0 3.6.57 1 1 0 0 1 1 1V20a1 1 0 0 1-1 1A17 17 0 0 1 3 4a1 1 0 0 1 1-1h3.5a1 1 0 0 1 1 1c0 1.25.2 2.45.57 3.57a1 1 0 0 1-.25 1z"/></svg>
        <span>15027390614</span>
      </li>
      <li class="contact__item">
        <svg class="contact__icon" viewBox="0 0 24 24" aria-hidden="true"><path d="M2 5h20v14H2z M2 5l10 8 10-8" fill="var(--ink)"/><path d="M2 5l10 8 10-8" fill="none" stroke="var(--card)" stroke-width="2"/></svg>
        <span>mathqt@sampleinbox.com</span>
      </li>
    </ul>
  </section>
</main>
</body>
</html>
```